Redesign of Form/Document Navigation Page

I need a redesign of our document and navigation bar on the left. We want the same navigation bar layout/setup but want the buttons and typography to be simple and matching all over. The form needs to be aesthetically pleasing and fit within the page.

1st attachment is our Direct Deposit and the second is the form continued.

```html
<!DOCTYPE html>
<html lang="en">
<head>
<meta charset="utf-8">
<title>Employee Direct Deposit Enrollment Form</title>
<link href="https://fonts.googleapis.com/css2?family=Catamaran:wght@500;600;700;800&family=Open+Sans:ital,wght@0,400;0,600;0,700;1,600&display=swap" rel="stylesheet">
<style>
:root{
  --navy:#2f2d6e;
  --gold:#f0b323;
  --ink:#2d2d2d;
  --text:#555;
  --line:#d6d6d6;
  --page:#f4f4f4;
  --white:#fff;
}
*{box-sizing:border-box;margin:0;padding:0}
html,body{width:1169px;height:1200px;overflow:hidden}
body{font-family:"Open Sans",sans-serif;background:var(--page);color:var(--text);position:relative}
.topbar{position:absolute;top:0;left:0;width:1169px;height:82px;background:var(--white);border-top:3px solid var(--navy);border-bottom:1px solid var(--line)}
.brand{position:absolute;left:95px;top:14px;display:flex;align-items:center;gap:8px;font-family:"Catamaran",sans-serif;font-weight:800;color:var(--gold);font-size:27px;line-height:22px;text-transform:uppercase}
.brand-mark{width:46px;height:46px;border-radius:50%;background:var(--navy);flex:none}
.mainnav{position:absolute;left:407px;top:29px;font-family:"Catamaran",sans-serif;font-weight:700;font-size:15px;color:var(--ink)}
.mainnav .active{color:var(--gold)}
.mainnav .sep{margin:0 12px}
.userbox{position:absolute;left:764px;top:19px;width:165px;height:42px;border:1px solid #bbb;border-radius:3px;display:flex;align-items:center;padding:0 6px;gap:9px;font-size:13px;color:var(--ink)}
.avatar{width:29px;height:29px;border-radius:50%;background:linear-gradient(#8a7a6e,#4c4440);flex:none}
.userbox svg{margin-left:auto}
.backlink{position:absolute;left:967px;top:31px;font-family:"Catamaran",sans-serif;font-weight:700;font-size:13px;color:var(--ink);text-decoration:underline}
.sidebar{position:absolute;left:96px;top:125px;width:309px;height:960px;background:var(--white);border:1px solid var(--line);padding:6px}
.navitem{height:85px;border:1px solid var(--line);margin-bottom:8px;display:flex;align-items:center;padding-left:14px;gap:19px;font-family:"Catamaran",sans-serif;font-weight:600;font-size:18px;color:var(--ink)}
.navitem .ic{width:74px;height:74px;border-radius:50%;border:2px solid #e2e2e2;display:flex;align-items:center;justify-content:center;flex:none;background:var(--white)}
.navitem.current{background:var(--navy);border-color:var(--navy);color:var(--white)}
.navitem.current .ic{border:2px solid var(--white);box-shadow:inset 0 0 0 3px var(--navy),inset 0 0 0 40px var(--white)}
.formcard{position:absolute;left:438px;top:125px;width:634px;height:960px;background:var(--white);border:1px solid var(--line)}
.formtitle{height:50px;background:var(--ink);color:var(--white);font-family:"Catamaran",sans-serif;font-weight:800;font-size:25px;text-align:center;line-height:54px}
.section{padding:0 19px;border-bottom:1px solid var(--line)}
.intro{padding-top:26px;padding-bottom:27px}
p{font-size:12px;line-height:23.4px}
.intro p+p{margin-top:23px}
.attach{margin-top:21px;border:1px solid var(--line);height:96px;text-align:center;padding-top:12px;font-family:"Catamaran",sans-serif;font-weight:600;font-size:15px;color:var(--ink)}
.btn{display:inline-block;margin-top:8px;width:83px;height:35px;border:1px solid #bbb;border-radius:3px;color:var(--gold);font-weight:800;font-size:13px;line-height:36px}
.account{padding-top:24px;padding-bottom:24px}
h2{font-family:"Open Sans",sans-serif;font-weight:700;font-size:14px;color:var(--ink);margin-bottom:10px}
.notice{font-style:italic;font-weight:600;font-size:13px;color:var(--ink);margin-top:12px}
.radios{display:flex;gap:22px;margin-top:14px;font-size:12px}
.radio{display:flex;align-items:center;gap:10px}
.radio i{width:18px;height:18px;border:2px solid #aaa;border-radius:50%}
.grid3{display:grid;grid-template-columns:189px 189px 189px;gap:16px;margin-top:22px}
label{font-size:12px;display:block;margin-bottom:11px}
.field{height:27px;border:1px solid #aaa}
.grid2{display:grid;grid-template-columns:189px 393px;gap:16px;margin-top:14px}
.amountrow{display:flex;align-items:center;margin-top:17px;font-size:12px;gap:22px}
.amount{margin-left:auto;display:flex;align-items:center;gap:12px}
.amount .field{width:170px;font-size:13px;color:var(--ink);padding:4px 8px}
.legal{border-bottom:none;padding-top:25px}
.legal h3{font-size:13px;font-weight:600;color:var(--ink);margin-bottom:9px}
.legal h3 b{font-weight:700}
.footer{position:absolute;left:0;top:1141px;width:1169px;height:59px;background:var(--ink);color:var(--white);font-size:12px}
.footer .copy{position:absolute;left:96px;top:22px}
.social{position:absolute;left:923px;top:14px;display:flex;gap:8px}
.social span{width:31px;height:31px;border-radius:50%}
</style>
</head>
<body>
<header class="topbar">
  <div class="brand"><span class="brand-mark"></span><span>Summit<br>Patrol Services</span></div>
  <nav class="mainnav"><span class="active">HOME</span><span class="sep">|</span><span>HELP</span></nav>
  <div class="userbox"><span class="avatar" role="img" aria-label="User profile photo"></span>Alex Morgan
    <svg width="20" height="20" viewBox="0 0 20 20"><path d="M6 4.5a7 7 0 1 0 8 0" fill="none" stroke="#2f2d6e" stroke-width="2.4" stroke-linecap="round"/><line x1="10" y1="2" x2="10" y2="9" stroke="#2f2d6e" stroke-width="2.4" stroke-linecap="round"/></svg>
  </div>
  <a class="backlink">BACK TO PROFILE</a>
</header>

<aside class="sidebar">
  <div class="navitem current"><span class="ic"><svg width="46" height="46" viewBox="0 0 46 46"><line x1="23" y1="4" x2="23" y2="20" stroke="#f0b323" stroke-width="3"/><path d="M16 14l7 7 7-7" fill="none" stroke="#f0b323" stroke-width="3"/><ellipse cx="13" cy="30" rx="8" ry="3.5" fill="#f0b323"/><ellipse cx="13" cy="36" rx="8" ry="3.5" fill="#f0b323"/><ellipse cx="33" cy="28" rx="8" ry="3.5" fill="#f0b323"/><ellipse cx="33" cy="34" rx="8" ry="3.5" fill="#f0b323"/><ellipse cx="23" cy="38" rx="8" ry="3.5" fill="#f0b323"/></svg></span>Direct Deposit</div>
  <div class="navitem"><span class="ic"><svg width="40" height="40" viewBox="0 0 40 40"><rect x="10" y="8" width="20" height="28" fill="#2f2d6e"/><circle cx="20" cy="12" r="5" fill="#2f2d6e" stroke="#fff" stroke-width="1.5"/><g stroke="#fff" stroke-width="1.5"><line x1="13" y1="22" x2="27" y2="22"/><line x1="13" y1="27" x2="27" y2="27"/><line x1="13" y1="31" x2="27" y2="31"/></g></svg></span>Change W-4</div>
  <div class="navitem"><span class="ic"><svg width="40" height="40" viewBox="0 0 40 40"><path d="M13 11a13 13 0 1 1 0 18" fill="none" stroke="#2f2d6e" stroke-width="3"/><path d="M4 17h12v-5l9 8-9 8v-5H4z" fill="#2f2d6e"/></svg></span>Labour Code</div>
  <div class="navitem"><span class="ic"><svg width="40" height="40" viewBox="0 0 40 40"><circle cx="18" cy="11" r="6" fill="#2f2d6e"/><path d="M6 34c0-10 5-15 12-15s12 5 12 15z" fill="#2f2d6e"/><circle cx="27" cy="27" r="6" fill="#fff" stroke="#2f2d6e" stroke-width="2"/><line x1="27" y1="25" x2="27" y2="30" stroke="#2f2d6e" stroke-width="2"/></svg></span>Personal Information</div>
  <div class="navitem"><span class="ic"><svg width="46" height="40" viewBox="0 0 46 40"><g fill="#2f2d6e"><path d="M10 12l3 7h7l-6 4 2 7-6-4-6 4 2-7-6-4h7z"/><path d="M36 12l3 7h7l-6 4 2 7-6-4-6 4 2-7-6-4h7z"/><path d="M23 8l4 9h9l-7 6 3 9-9-6-9 6 3-9-7-6h9z"/></g></svg></span>Appraisal and Review</div>
  <div class="navitem"><span class="ic"><svg width="40" height="40" viewBox="0 0 40 40"><rect x="11" y="7" width="22" height="27" fill="none" stroke="#2f2d6e" stroke-width="2.5"/><path d="M7 12v26h22" fill="none" stroke="#2f2d6e" stroke-width="2.5"/><g stroke="#2f2d6e" stroke-width="2.5"><line x1="15" y1="14" x2="29" y2="14"/><line x1="15" y1="20" x2="29" y2="20"/><line x1="15" y1="26" x2="29" y2="26"/></g></svg></span>Write Up-Slip</div>
  <div class="navitem"><span class="ic"><svg width="44" height="40" viewBox="0 0 44 40"><g fill="#2f2d6e"><circle cx="11" cy="14" r="5"/><circle cx="33" cy="14" r="5"/><path d="M2 32c0-8 4-12 9-12s9 4 9 12z"/><path d="M24 32c0-8 4-12 9-12s9 4 9 12z"/><circle cx="22" cy="12" r="6" stroke="#fff" stroke-width="1.5"/><path d="M11 34c0-9 5-14 11-14s11 5 11 14z" stroke="#fff" stroke-width="1.5"/></g></svg></span>Employee Performance</div>
</aside>

<main class="formcard">
  <h1 class="formtitle">EMPLOYEE DIRECT DEPOSIT ENROLLMENT FORM</h1>
  <section class="section intro">
    <p>To enroll in Direct Deposit, simply fill out this form. Attach a voided check for each checking account - not a deposit slip. If depositing to a savings account, ask your bank to gig a you the Routing/Transit Number for your account. It isn't always the same as the number on a swings deposit slip. This will help ensure that yrou are paid correctly. Once filled out, accounting will review our information for processing. Once processed, you will receive an email confirmation with details.</p>
    <p>Employees must attach a voided check for each of their accounts to help verify their account numbers and</p>
    <div class="attach">Attach A Voided Check Or Bank Deposit Form for the Account<br><span class="btn">REFRESH</span></div>
  </section>
  <section class="section account">
    <h2>ACCOUNT INFORMATION</h2>
    <p>The last item must be for ihe remaining amount owed to you. To distribute to more account, please complete another form. Make sure to indicate what kind of account, along with enrolling or declining. ...</p>
    <div class="notice">**NOTIFY PAYROLL IMMEDIATELY IF YOU CLOSE OR CHANGE BANK ACCOUNT**</div>
    <div class="radios"><span class="radio"><i></i>New Enrollment</span><span class="radio"><i></i>Change Enrollment</span><span class="radio"><i></i>Cancel Enrollment</span></div>
    <div class="grid3">
      <div><label>Bank Name:</label><div class="field"></div></div>
      <div><label>City:</label><div class="field"></div></div>
      <div><label>State:</label><div class="field"></div></div>
    </div>
    <div class="grid2">
      <div><label>Routing Transit #:</label><div class="field"></div></div>
      <div><label>Account Number:</label><div class="field"></div></div>
    </div>
    <div class="amountrow"><span class="radio"><i></i>Checking</span><span class="radio"><i></i>Savings</span>
      <span class="amount">Amount <span class="field">100</span>%</span></div>
  </section>
  <section class="section legal">
    <h3><b>IMPORTANT!</b> Please read and sign before completing and submitting.</h3>
    <p>I hereby authorize SUMMIT PATROL SERVICES M deposit any amounts owed me, as instructed by my employer, by initiating credit entries to my account at the financial institution (hereinafter 'Tank.) indicated on this form. Further, I authorize Bank to accept and to credit any credit entries indicated by SUMMIT PATROL SERVICES to my account In the even that SUMMIT PATROL SERVICES deposits funds erroneously into my account I authorize SUMMIT PATROL SERVICES to.</p>
  </section>
</main>

<footer class="footer">
  <span class="copy">© 2016, Summit Patrol Services. All rights reserved.</span>
  <div class="social"><span style="background:#3b5ea8"></span><span style="background:#4ab0e6"></span><span style="background:#e0383b"></span><span style="background:#1c6fa5"></span></div>
</footer>
</body>
</html>
```